Homemaking training schools needs a Business Card design

Designer, Hello!

No special requirements, good-looking enough.
--------------------------------------------------------------------------

Name: Marcus Dole
Chairman
Tel: 0574-71948263
Mobile: 13857420916
Email: kelvora@mailnest.example
Web: www.prt2019.example
Add: No.258, LanpingJie, BeiyuanQu, Ningbo, Zhejiang

LOGO
Ningbo PRT Homemaking Training School

Target Market(s)

pregnant women, mothers, infants, the elderly and families, including cleaning, cooking, nursing training.

Industry/Entity Type

Business

Contact Information for Business Card

Name: Marcus Dole
Chairman
Tel: 0574-71948263
Mobile: 13857420916
Email: kelvora@mailnest.example
Web: www.prt2019.example

LOGO

Font styles to use
Serif
Sans Serif
Decorative

Requirements
Nice to have
• Feels: clean, specifications, safety, comfort, warmth and happiness.

```html
<!DOCTYPE html>
<html lang="en">
<head>
<meta charset="utf-8">
<title>PeiRongTang Training &amp; Services – Business Card</title>
<link rel="stylesheet" href="https://fonts.googleapis.com/css2?family=Montserrat:wght@400;600;700;800&display=swap">
<style>
  :root {
    --blue: #1273bd;
    --pink: #e5158c;
    --white: #ffffff;
    --stage: #2b2b2d;
    --ink-blue: #1470b8;
  }
  * { box-sizing: border-box; margin: 0; padding: 0; }
  html, body { width: 1200px; height: 900px; overflow: hidden; }
  body {
    background: var(--stage);
    font-family: "Montserrat", Arial, sans-serif;
    position: relative;
  }
  .card {
    position: absolute;
    left: 260px;
    width: 680px;
    height: 390px;
    border-radius: 26px;
    overflow: hidden;
  }
  .card-back { top: 40px; background: var(--blue); }
  .card-front { top: 470px; background: var(--white); }

  /* back side */
  .back-brand {
    position: absolute;
    left: 0; right: 0; top: 140px;
    display: flex; align-items: center; justify-content: center; gap: 14px;
  }
  .brand-dot {
    width: 30px; height: 30px; border-radius: 50%;
    background: var(--pink);
  }
  .back-brand .brand-name {
    font-size: 46px; font-weight: 700; color: var(--white); letter-spacing: 0.5px;
  }
  .back-url {
    position: absolute; left: 0; right: 0; top: 300px;
    text-align: center; color: var(--white);
    font-size: 17px; font-weight: 700; letter-spacing: 0.5px;
  }

  /* front side */
  .front-shape { position: absolute; inset: 0; }
  .front-brand {
    position: absolute; left: 44px; top: 150px; width: 330px;
    color: var(--white);
  }
  .front-brand .brand-row { display: flex; align-items: center; gap: 10px; }
  .front-brand .brand-dot { width: 18px; height: 18px; }
  .front-brand .brand-name { font-size: 40px; font-weight: 700; }
  .tagline {
    display: flex; align-items: center; gap: 8px; margin-top: 6px;
    font-size: 17px; font-weight: 400;
  }
  .tagline::before, .tagline::after {
    content: ""; flex: 1; height: 1.5px; background: var(--white);
  }
  .contact {
    position: absolute; left: 432px; top: 70px; width: 240px;
    color: var(--ink-blue);
  }
  .person-name { font-size: 25px; font-weight: 800; letter-spacing: 0.5px; }
  .person-role { font-size: 12px; font-weight: 700; color: var(--pink); letter-spacing: 1px; margin-top: 2px; }
  .address { font-size: 12.5px; font-weight: 600; margin-top: 12px; line-height: 1.45; }
  .contact-list { list-style: none; margin-top: 6px; }
  .contact-list li {
    display: flex; align-items: center; gap: 8px;
    font-size: 12.5px; font-weight: 700; line-height: 1.6;
  }
  .contact-list svg { width: 11px; height: 11px; flex: none; }
</style>
</head>
<body>
  <section class="card card-back" aria-label="Card back">
    <div class="back-brand">
      <span class="brand-dot"></span>
      <span class="brand-name">PeiRongTang</span>
    </div>
    <p class="back-url">www.prt2019.example</p>
  </section>

  <section class="card card-front" aria-label="Card front">
    <svg class="front-shape" viewBox="0 0 680 390" preserveAspectRatio="none" aria-hidden="true">
      <path d="M0 0 H250 C350 20 415 140 415 240 C415 300 400 350 385 390 H0 Z" fill="var(--blue)"/>
      <path d="M250 -2 C358 18 426 140 426 240 C426 300 412 350 396 392" fill="none" stroke="var(--pink)" stroke-width="3"/>
    </svg>

    <div class="front-brand">
      <div class="brand-row">
        <span class="brand-dot"></span>
        <span class="brand-name">PeiRongTang</span>
      </div>
      <p class="tagline">Training &amp; Services</p>
    </div>

    <div class="contact">
      <h1 class="person-name">MARCUS DOLE</h1>
      <p class="person-role">CHAIRMAN</p>
      <p class="address">258, LanpingJie<br>BeiyuanQu, Ningbo, Zhejiang</p>
      <ul class="contact-list">
        <li><svg viewBox="0 0 12 12"><path d="M2.5 1 L4.5 1 L5.2 3.6 L4 4.6 C4.6 6 6 7.4 7.4 8 L8.4 6.8 L11 7.5 L11 9.5 C11 10.3 10.3 11 9.5 11 C5 11 1 7 1 2.5 C1 1.7 1.7 1 2.5 1 Z" fill="var(--pink)"/></svg>0574-71948263</li>
        <li><svg viewBox="0 0 12 12"><rect x="3" y="0.8" width="6" height="10.4" rx="1.2" fill="none" stroke="var(--pink)" stroke-width="1.4"/><circle cx="6" cy="9.3" r="0.7" fill="var(--pink)"/></svg>13857420916</li>
        <li><svg viewBox="0 0 12 12"><rect x="0.8" y="2.3" width="10.4" height="7.4" rx="1" fill="none" stroke="var(--pink)" stroke-width="1.3"/><path d="M1 2.8 L6 6.6 L11 2.8" fill="none" stroke="var(--pink)" stroke-width="1.3"/></svg>kelvora@mailnest.example</li>
        <li><svg viewBox="0 0 12 12"><circle cx="6" cy="6" r="5" fill="none" stroke="var(--pink)" stroke-width="1.3"/><path d="M1 6 H11 M6 1 C3.5 3.5 3.5 8.5 6 11 M6 1 C8.5 3.5 8.5 8.5 6 11" fill="none" stroke="var(--pink)" stroke-width="1"/></svg>www.prt2019.example</li>
      </ul>
    </div>
  </section>
</body>
</html>
```